Wellness, Meaning, and the Inner Journey Research Program Website

Overview: This website will serve a new research program (Wellness, Meaning, and the Inner Journey) at the Harrowgate University School of Medicine. I want a clean, intuitive design that has a navigation bar, but uses icons/graphic buttons to link to the main pages. In an attached Word document, I have provided a basic information architecture for the site, understanding that this project would just generate graphics and code for the 3 pages. I highlighted the 3 pages I'd like designed.
Target market: People who want to participate in our research, or contribute grant funding to specific projects.
Number of page: The design project focuses on 3 pages, but the site must accommodate 6 pages with top-level links. See attached Word doc.
Logo and website header: Please integrate our logo in the header. I've uploaded it as a png file--both with the name of the website and with just the logo image. I imaging the logo would look great in a banner set against an image of a mountain. The two main design themes I want to see included are nature and healthcare.
Text content: I have not yet provided text. Use some dummy text.
Technical Specifications:
- Build using WordPress. We will host this site ourselves on NetHarbor using WordPress.
- The design package must be coded.
- The template must be responsive to different platforms (e.g., computer, mobile phone, iPad).
Thank you! I look forward to seeing your designs.
- Ned

```html
<!DOCTYPE html>
<html lang="en">
<head>
<meta charset="utf-8">
<title>Wellness, Meaning, and the Inner Journey – The Research Program</title>
<link href="https://fonts.googleapis.com/css2?family=Roboto:wght@300;400;500;700&family=Roboto+Condensed:wght@400;700&family=Great+Vibes&display=swap" rel="stylesheet">
<style>
:root{
  --green:#3aa655;
  --teal:#178a86;
  --blue:#1563a6;
  --navy:#0f4f8c;
  --ink:#333a40;
  --muted:#6b7379;
  --light:#f2f3f4;
  --line:#dcdfe2;
  --white:#ffffff;
}
*{box-sizing:border-box;margin:0;padding:0}
html,body{width:1200px;height:2816px;overflow:hidden}
body{font-family:"Roboto",Arial,sans-serif;color:var(--ink);background:var(--white);position:relative}

/* header */
.site-header{position:absolute;top:0;left:0;width:1200px;height:120px;background:var(--white);z-index:3}
.main-nav{position:absolute;top:50px;left:0;width:1200px;display:flex;justify-content:center;align-items:center;font-size:17px;font-weight:500}
.main-nav a{color:var(--ink);text-decoration:none;margin:0 28px}
.main-nav a.active{color:var(--green);border-bottom:2px solid var(--green);padding-bottom:6px}
.brand{display:flex;align-items:center;gap:8px;margin:0 40px;color:var(--navy);font-weight:700;font-size:18px}
.brand-dot{width:26px;height:26px;border-radius:50%;background:var(--green)}

/* hero */
.hero{position:absolute;top:120px;left:0;width:1200px;height:500px;
  background:linear-gradient(180deg,#cfe3ef 0%,#b7cbd6 14%,#a8654a 36%,#8c4630 55%,#4c6e3a 78%,#2f5a2c 100%)}
.hero-eyebrow{position:absolute;top:252px;width:1200px;text-align:center;color:var(--white);font-size:26px;font-weight:300;letter-spacing:.5px}
.hero-title{position:absolute;top:296px;width:1200px;text-align:center;color:var(--white);font-family:"Roboto Condensed",sans-serif;font-weight:700;font-size:54px;letter-spacing:1px}
.hero-links{position:absolute;top:400px;left:0;width:1200px;display:flex;justify-content:center;gap:76px}
.hero-link{width:180px;text-align:center;color:var(--white);font-size:15px;font-weight:700;text-transform:uppercase;white-space:nowrap}
.hero-link .ring{width:96px;height:96px;border:3px solid var(--white);border-radius:50%;margin:0 auto 16px;display:flex;align-items:center;justify-content:center}

/* people */
.people-photo-back{position:absolute;top:820px;left:100px;width:310px;height:400px;background:linear-gradient(160deg,var(--teal),var(--blue))}
.people-photo{position:absolute;top:732px;left:140px;width:370px;height:450px;background:var(--white);padding:12px;box-shadow:0 4px 14px rgba(0,0,0,.2)}
.people-photo div{width:100%;height:100%;background:linear-gradient(140deg,#2d5f9a 0%,#6e95c0 40%,#dfe7ef 70%,#b9c6d2 100%)}
.section-script{font-family:"Great Vibes",cursive;font-size:76px;color:var(--blue);font-weight:400}
.people-title{position:absolute;top:744px;left:576px}
.divider-icon{width:18px;height:16px;border:2px solid var(--muted);border-radius:2px}
.people-divider{position:absolute;top:840px;left:690px;display:flex;align-items:center}
.people-text{position:absolute;top:870px;left:576px;width:560px;font-size:14.5px;line-height:24px;color:var(--muted)}
.people-links{position:absolute;top:1040px;left:600px;display:flex;gap:58px}
.people-link{width:130px;text-align:center;font-size:14px;font-weight:500;color:var(--ink)}
.people-link svg{display:block;margin:0 auto 14px}

/* research */
.research{position:absolute;top:1340px;left:0;width:1200px;height:540px;
  background:linear-gradient(170deg,#1a8b87 0%,#3ca66c 30%,#1f8f8c 55%,#1563a6 100%)}
.research-title{position:absolute;top:1460px;width:1200px;text-align:center;color:var(--white);font-size:42px;font-weight:300}
.research-divider{position:absolute;top:1536px;left:591px}
.research-text{position:absolute;top:1600px;left:140px;width:920px;text-align:center;color:var(--white);font-size:14px;line-height:24px;opacity:.95}
.btn{position:absolute;top:1728px;left:542px;width:116px;height:40px;border-radius:20px;background:var(--navy);color:var(--white);font-size:14px;display:flex;align-items:center;justify-content:center}

/* faq */
.faq{position:absolute;top:1880px;left:0;width:1200px;height:740px;background:var(--light)}
.faq-art{position:absolute;top:2080px;left:60px;width:380px;height:270px;border-radius:6px;background:linear-gradient(150deg,#e9eef2 0%,#c9dbe8 60%,#8fc0d8 100%)}
.faq-list{position:absolute;top:2010px;left:480px;width:660px}
.faq-item{background:var(--white);border:1px solid var(--line);margin-bottom:14px}
.faq-q{height:60px;display:flex;justify-content:space-between;align-items:center;padding:0 22px;font-size:16px;color:var(--ink);background:#e6e8ea}
.faq-a{padding:22px;font-size:14px;line-height:24px;color:var(--muted);background:var(--white)}
.faq-toggle{font-size:22px;color:var(--muted);font-weight:300}

/* footer */
.site-footer{position:absolute;top:2620px;left:0;width:1200px;height:144px;background:var(--blue);color:var(--white)}
.newsletter{position:absolute;top:30px;left:54px}
.footer-heading{font-size:24px;font-weight:300}
.footer-heading b{font-weight:700}
.newsletter-form{display:flex;margin-top:18px}
.newsletter-form span{width:244px;height:36px;background:var(--white);color:#999;font-size:13px;display:flex;align-items:center;padding-left:12px}
.newsletter-form strong{width:112px;height:36px;background:var(--green);font-size:13px;font-weight:700;display:flex;align-items:center;justify-content:center}
.footer-brand{position:absolute;top:56px;left:0;width:1200px;display:flex;justify-content:center;align-items:center;gap:10px;font-size:20px;font-weight:700}
.footer-brand .dot{width:30px;height:30px;border-radius:50%;background:var(--white)}
.social{position:absolute;top:30px;right:54px;text-align:right}
.social-row{display:flex;gap:12px;margin-top:18px}
.social-row span{width:36px;height:36px;border-radius:50%;background:var(--white)}
.bottom-bar{position:absolute;top:2764px;left:0;width:1200px;height:52px;background:var(--green);color:var(--white);font-size:13px;display:flex;justify-content:space-between;align-items:center;padding:0 54px}
.bottom-bar nav span{margin-right:22px}
</style>
</head>
<body>

<header class="site-header">
  <nav class="main-nav">
    <a class="active">Home</a><a>People</a><a>Projects</a>
    <span class="brand"><span class="brand-dot"></span>Inner Journey</span>
    <a>FAQ's</a><a>Resources</a><a>Contact</a>
  </nav>
</header>

<section class="hero" role="img" aria-label="Photograph of red sandstone rock towers above a green forest valley under a pale sky"></section>
<div class="hero-eyebrow">Wellness, Meaning, and the Inner Journey</div>
<h1 class="hero-title">THE RESEARCH PROGRAM</h1>
<div class="hero-links">
  <div class="hero-link"><div class="ring"><svg width="46" height="40" viewBox="0 0 46 40" fill="none" stroke="#fff" stroke-width="3"><circle cx="15" cy="11" r="7"/><circle cx="32" cy="11" r="7"/><path d="M2 38c0-9 6-14 13-14s13 5 13 14M20 30c2-4 7-6 12-6 7 0 12 5 12 14"/></svg></div>People</div>
  <div class="hero-link"><div class="ring"><svg width="48" height="38" viewBox="0 0 48 38" fill="none" stroke="#fff" stroke-width="3"><path d="M24 8C18 3 9 3 3 5v28c6-2 15-2 21 3 6-5 15-5 21-3V5c-6-2-15-2-21 3zM24 8v28"/></svg></div>Research Projects</div>
  <div class="hero-link"><div class="ring"><svg width="46" height="40" viewBox="0 0 46 40" fill="none" stroke="#fff" stroke-width="3"><path d="M4 18c0-8 9-14 19-14s19 6 19 14-9 14-19 14c-3 0-6-1-8-2l-9 5 3-8c-3-2-5-6-5-9z"/><text x="23" y="25" fill="#fff" stroke="none" font-size="16" font-weight="700" text-anchor="middle" font-family="Roboto">?</text></svg></div>FAQ's</div>
</div>

<div class="people-photo-back"></div>
<div class="people-photo"><div role="img" aria-label="Photograph from above of a researcher typing at a laptop beside printed charts"></div></div>
<h2 class="section-script people-title">People</h2>
<div class="people-divider"><span class="divider-icon"></span></div>
<p class="people-text">Lorem ipsum dolor sit amet, consectetur adipiscing elit. Sed sodales maximus sapien, at posuere elit finibus iaculis. Donec tincidunt erat a nunc luctus posuere, a efficitur massa fermentum. Praesent ultrices quam in fermentum ultrices. Quisque nisl augue, cursus in rhoncus vitae, tempus a mi. Praesent tempus varius dignissim.</p>
<div class="people-links">
  <div class="people-link"><svg width="44" height="44" viewBox="0 0 44 44" fill="none" stroke="#178a86" stroke-width="2.5"><circle cx="22" cy="22" r="19"/><circle cx="22" cy="17" r="5"/><path d="M13 32c2-6 6-8 9-8s7 2 9 8"/></svg>Research Team</div>
  <div class="people-link"><svg width="50" height="44" viewBox="0 0 50 44" fill="none" stroke="#178a86" stroke-width="2.5"><circle cx="25" cy="10" r="5"/><circle cx="10" cy="16" r="4"/><circle cx="40" cy="16" r="4"/><path d="M4 40 L25 22 L46 40Z"/></svg>Advisory committee</div>
  <div class="people-link"><svg width="50" height="44" viewBox="0 0 50 44" fill="none" stroke="#178a86" stroke-width="2.5"><path d="M3 20l10-8 8 4 8-4 6 0 12 8-10 12-12 4-10-6z"/><path d="M21 16l8 8"/></svg>Partners</div>
</div>

<section class="research" role="img" aria-label="Faint photograph of hands working over papers beneath a teal, green and blue colour wash"></section>
<h2 class="research-title">Research Projects</h2>
<div class="research-divider"><span class="divider-icon" style="border-color:#fff;display:block"></span></div>
<p class="research-text">Aenean efficitur pretium viverra. Aliquam rutrum mauris nunc, et tincidunt ante eget enim interdum mattis at id sem. Aenean malesuada quis arcu et vulputate. Vivamus tristique odio aliquam ultrices posuere, vel porta nisi. Aliquam et malesuada quam et diam imperdiet. Praesent cursus lorem egestas. Donec tempor dolor sit amet aliquet pharetra.</p>
<div class="btn">Read More</div>

<section class="faq"></section>
<div class="faq-art" role="img" aria-label="Illustration of the word FAQ with a small figure on a ladder and question marks"></div>
<div class="faq-list">
  <div class="faq-item">
    <div class="faq-q">Q1: What makes this project unique? <span class="faq-toggle">⌃</span></div>
    <div class="faq-a">Aenean efficitur pretium viverra. Aliquam rutrum mauris nunc, et tincidunt ante eget enim interdum. Integer vitae nisi eget enim imperdiet mattis at id sem. Aenean malesuada quis arcu et vulputate.</div>
  </div>
  <div class="faq-item"><div class="faq-q">Q2: Does this project assume that the impact of religion is always positive? <span class="faq-toggle">+</span></div></div>
  <div class="faq-item"><div class="faq-q">Q3: How can I collaborate? <span class="faq-toggle">+</span></div></div>
  <div class="faq-item"><div class="faq-q">Q4: Will Harrowgate faculty lead all projects? <span class="faq-toggle">+</span></div></div>
</div>

<footer class="site-footer">
  <div class="newsletter">
    <div class="footer-heading">Signup <b>Newsletter</b> :</div>
    <div class="newsletter-form"><span>Your Email</span><strong>SUBSCRIBE</strong></div>
  </div>
  <div class="footer-brand"><span class="dot"></span>Inner Journey</div>
  <div class="social">
    <div class="footer-heading">Stay <b>In Touch</b> :</div>
    <div class="social-row"><span></span><span></span><span></span><span></span><span></span></div>
  </div>
</footer>
<div class="bottom-bar">
  <nav><span>Home</span><span>/</span><span>People</span><span>/</span><span>Research Projects</span><span>/</span><span>FAQ's</span><span>/</span><span>Resources</span><span>/</span><span>Contact</span></nav>
  <div>Copyright © 2016-2017. All rights reserved.</div>
</div>

</body>
</html>
```